Clear sticker design for packaging

I need 4” diameter clear stickers designed for birthdays, thank you , teachers day and all the other special days to complete my gift packaging. They will go on the top of each tube to differentiate each gift for each occasion. Our design is on craft paper and I’ve uploaded a few examples of what we are trying to achieve. Last picture is the top of our tube where the stickers will be placed. We don’t want too much color unless for Christmas and Valentine’s Day maybe! We are working with black and gold or a mixture of both mostly

```html
<!DOCTYPE html>
<html lang="en">
<head>
<meta charset="UTF-8">
<title>Thank You Sticker</title>
<link rel="stylesheet" href="https://fonts.googleapis.com/css2?family=Dancing+Script:wght@700&display=swap">
<style>
  :root {
    --backdrop: #d9d9d9;
    --sticker-black: #000000;
    --copper: #c98a66;
    --copper-deep: #b4714c;
    --gold: #efcf78;
    --leaf-olive: #6f7444;
    --bloom-orange: #b8650f;
    --petal-beige: #e4c3a7;
  }
  html, body {
    margin: 0;
    padding: 0;
    width: 1200px;
    height: 669px;
    overflow: hidden;
    background: var(--backdrop);
  }
  .canvas {
    position: relative;
    width: 1200px;
    height: 669px;
    background: var(--backdrop);
  }
  .sticker {
    position: absolute;
    left: 320px;
    top: 54px;
    width: 560px;
    height: 560px;
    border-radius: 50%;
    background: var(--sticker-black);
    overflow: hidden;
    box-shadow: 0 2px 4px rgba(0,0,0,0.18);
  }
  .sticker-florals {
    position: absolute;
    inset: 0;
    width: 560px;
    height: 560px;
  }
  .greeting {
    margin: 0;
    font-family: "Dancing Script", cursive;
    font-weight: 700;
  }
  .greeting-line {
    position: absolute;
    display: block;
    line-height: 1.25;
    padding: 0 30px 40px;
    letter-spacing: -3px;
    white-space: nowrap;
    background: linear-gradient(180deg, var(--copper) 10%, var(--copper-deep) 40%, var(--gold) 62%, var(--copper) 85%);
    -webkit-background-clip: text;
    background-clip: text;
    color: transparent;
  }
  .greeting-thank {
    left: 50%;
    top: 92px;
    transform: translateX(-50%);
    font-size: 156px;
  }
  .greeting-you {
    left: 50%;
    top: 236px;
    transform: translateX(-44%);
    font-size: 146px;
  }
</style>
</head>
<body>
  <main class="canvas">
    <div class="sticker">
      <svg class="sticker-florals" viewBox="0 0 560 560" xmlns="http://www.w3.org/2000/svg">
        <defs>
          <radialGradient id="floral-top-tones" cx="0.5" cy="0.5" r="0.5">
            <stop offset="0" stop-color="#b8650f" stop-opacity="0.9"/>
            <stop offset="0.45" stop-color="#8a6a3a" stop-opacity="0.75"/>
            <stop offset="0.8" stop-color="#6f7444" stop-opacity="0.35"/>
            <stop offset="1" stop-color="#6f7444" stop-opacity="0"/>
          </radialGradient>
          <radialGradient id="floral-bottom-tones" cx="0.5" cy="0.5" r="0.5">
            <stop offset="0" stop-color="#b8650f" stop-opacity="0.85"/>
            <stop offset="0.45" stop-color="#7d6d3c" stop-opacity="0.7"/>
            <stop offset="0.8" stop-color="#6f7444" stop-opacity="0.3"/>
            <stop offset="1" stop-color="#6f7444" stop-opacity="0"/>
          </radialGradient>
        </defs>
        <ellipse role="img" aria-label="Top spray of autumn flowers, monstera leaves and berry sprigs" cx="330" cy="55" rx="250" ry="95" fill="url(#floral-top-tones)"/>
        <ellipse role="img" aria-label="Bottom spray of autumn flowers, monstera leaves and berry sprigs" cx="240" cy="520" rx="230" ry="80" fill="url(#floral-bottom-tones)"/>
      </svg>
      <h1 class="greeting">
        <span class="greeting-line greeting-thank">thank</span>
        <span class="greeting-line greeting-you">you</span>
      </h1>
    </div>
  </main>
</body>
</html>
```